Feature Film "look book" digital brochure

Looking for a designer to create an edgy, gritty, eye popping visual representation of my film to get interest from investors, producers and actors. Basically it would introduce the project and in about 7-9 pages; give an overview of the film, why to invest, an artistic statement and potential casting ideas and an introduction to the key crew. I have included way more images than you would ever need in the files. I've also included samples for other films and a brochure someone already did for the film just to give you an idea of how it should be structured and the text content. Visually that piece is not a good guideline because it doesn't visually rep the film which is why I"m doing this contest!
The film is called 3 by 12: the sentence of an alcoholic teacher who commits a crime she can't remember and whose chance for survival depends on an ex-drug dealer and a basketball court.
Reason: I wanted people to have more time to send samples
Independent film investors, artists
Digital

```html
<!DOCTYPE html>
<html lang="en">
<head>
<meta charset="utf-8">
<title>3 by 12 — Look Book Cover</title>
<link rel="stylesheet" href="https://fonts.googleapis.com/css2?family=Rubik+Dirt&family=Open+Sans:wght@400&display=swap">
<style>
  :root {
    --page-bg: #d9dee3;
    --paper: #f7f7f5;
    --ink: #0c0c0c;
    --accent-red: #e3141b;
    --label-text: #ffffff;
    --shadow-dark: #141414;
    --ground: #4a4a3c;
    --sky-light: #fbfbfa;
  }
  html, body {
    margin: 0;
    padding: 0;
    width: 1200px;
    height: 840px;
    overflow: hidden;
    background: var(--page-bg);
  }
  .canvas {
    position: relative;
    width: 1200px;
    height: 840px;
  }
  .cover {
    position: absolute;
    left: 250px;
    top: 70px;
    width: 700px;
    height: 700px;
    background: var(--paper);
    overflow: hidden;
    box-shadow: 0 10px 30px rgba(0,0,0,0.25);
  }
  .cover-photo {
    position: absolute;
    inset: 0;
    background:
      linear-gradient(180deg, rgba(255,255,255,0) 78%, var(--ground) 100%),
      linear-gradient(90deg, var(--shadow-dark) 0%, #2a2a2a 24%, rgba(60,60,60,0.6) 36%, rgba(255,255,255,0) 48%),
      linear-gradient(180deg, var(--sky-light) 0%, #ececea 100%);
  }
  .title-block {
    position: absolute;
    left: 230px;
    top: 36px;
    width: 240px;
  }
  .title-rule {
    position: absolute;
    height: 10px;
    background: var(--ink);
  }
  .rule-top    { left: 10px;  top: 0;     width: 190px; }
  .rule-upper  { left: -20px; top: 145px; width: 230px; }
  .rule-middle { left: -40px; top: 258px; width: 270px; }
  .rule-bottom { left: -30px; top: 400px; width: 270px; }
  .title-word {
    position: absolute;
    margin: 0;
    font-family: "Rubik Dirt", "Arial Black", sans-serif;
    font-weight: 400;
    color: var(--ink);
    line-height: 1;
    text-transform: uppercase;
    text-align: center;
  }
  .word-number-top    { left: 60px; top: 16px;  width: 110px; font-size: 128px; }
  .word-connector     { left: 0;    top: 160px; width: 200px; font-size: 100px; }
  .word-number-bottom { left: -10px; top: 270px; width: 220px; font-size: 128px; }
  .corner-band {
    position: absolute;
    right: 0;
    top: 48px;
    width: 56px;
    height: 14px;
    background: var(--accent-red);
  }
  .label-box {
    position: absolute;
    left: 470px;
    top: 612px;
    width: 210px;
    height: 50px;
    background: var(--accent-red);
    display: flex;
    align-items: center;
    justify-content: center;
  }
  .label-text {
    font-family: "Open Sans", Arial, sans-serif;
    font-size: 24px;
    color: var(--label-text);
  }
</style>
</head>
<body>
<main class="canvas">
  <section class="cover">
    <div class="cover-photo" role="img" aria-label="High-contrast photograph of a player in silhouette on the left beside an outdoor basketball hoop against a bright sky, with a grassy court edge below"></div>

    <div class="title-block">
      <span class="title-rule rule-top"></span>
      <h1 class="title-word word-number-top">3</h1>
      <span class="title-rule rule-upper"></span>
      <p class="title-word word-connector">By</p>
      <span class="title-rule rule-middle"></span>
      <p class="title-word word-number-bottom">12</p>
      <span class="title-rule rule-bottom"></span>
    </div>

    <span class="corner-band"></span>

    <div class="label-box">
      <span class="label-text">Lorem Ipsum</span>
    </div>
  </section>
</main>
</body>
</html>
```